Heron Property Inspection business card

I am the principal inspector of Heron Property Inspections. I serve Northern Virginia from Winchester to Arlington.Associate, Federated Guild of Dwelling Examiners (FGDE)Graduate, FGDE Home Inspectors CourseNational Association of Home Inspectors ExamI'd like the business card to look more professional than comical.I pulled the attached picture off the web. I'd like to have something like that or an image of a house as my logo on the cards.

Target Market(s)

Persons who recently purchased a home.

Industry/Entity Type

Business

Contact Information for Business Card

Bob AllenBadger Home Inspections, LLC.4455 River RoadBluemont, Virginia 20135cell: 703-231-6680e-mail: tkmarlow@postvale.net

Font styles to use
Serif
Sans Serif

Requirements
Must have
• I'd like to have a logo, something that identifies me as a home inspector. The attached images are something that I'd like to have incorporated into my business card logo.
Nice to have
• I'd like a sketch of a house and/or a magnifying glass showing a house being inspected. The attached images are used as a suggestion only, I do not own the images.
Should not have
• Gimmicky stuff. I want to appear professional and trustworthy.

```html
<!DOCTYPE html>
<html lang="en">
<head>
<meta charset="utf-8">
<title>Heron Property Inspections – Business Card</title>
<link href="https://fonts.googleapis.com/css2?family=Arimo:wght@400;700&display=swap" rel="stylesheet">
<style>
  :root {
    --page: #e9e7e3;
    --card: #ffffff;
    --navy: #2b3f8c;
    --navy-light: #4a63b3;
    --ink-blue: #2d3d8a;
    --ink-dark: #3a3d45;
    --ink-grey: #5b5e66;
    --rule: #8a8d93;
  }
  * { margin: 0; padding: 0; box-sizing: border-box; }
  html, body {
    width: 1200px; height: 892px; overflow: hidden;
    background: var(--page);
    font-family: "Arimo", Arial, sans-serif;
  }
  .card {
    position: absolute; left: 75px; top: 146px;
    width: 1050px; height: 600px;
    background: var(--card);
    box-shadow: 0 6px 24px rgba(0,0,0,.18);
    overflow: hidden;
  }
  .brand-panel {
    position: absolute; left: 0; top: 0; width: 420px; height: 600px;
    background: linear-gradient(160deg, var(--navy) 0%, var(--navy) 55%, var(--navy-light) 100%);
  }
  .corner-notch { position: absolute; left: 0; top: 0; }
  .brand-box {
    position: absolute; left: 80px; top: 370px; width: 200px; height: 130px;
    background: var(--card);
    display: flex; align-items: center; justify-content: center;
    color: var(--ink-blue); font-weight: 700; font-size: 34px;
  }
  .identity { position: absolute; left: 470px; top: 80px; }
  .owner-name { color: var(--ink-blue); font-weight: 700; font-size: 46px; line-height: 1; }
  .company-name { color: var(--ink-dark); font-weight: 700; font-size: 26px; margin-top: 8px; }
  .role {
    position: absolute; left: 470px; top: 212px;
    border-left: 3px solid var(--ink-blue); padding-left: 18px;
  }
  .role-name { color: var(--ink-blue); font-size: 40px; line-height: 1; }
  .role-title { color: var(--ink-grey); font-size: 18px; margin-top: 4px; }
  .contact-row {
    position: absolute; left: 440px; width: 580px; height: 58px;
    border-top: 1.5px solid var(--rule);
    display: flex; align-items: center; padding-left: 16px;
    color: var(--ink-dark); font-size: 24px;
  }
  .contact-row.last { border-bottom: 1.5px solid var(--rule); }
  .contact-icon { position: absolute; left: -62px; top: 9px; }
</style>
</head>
<body>
  <div class="card">
    <div class="brand-panel">
      <svg class="corner-notch" width="420" height="200" viewBox="0 0 420 200">
        <polygon points="0,0 210,0 0,150" fill="#ffffff"/>
      </svg>
      <div class="brand-box">Heron</div>
    </div>

    <div class="identity">
      <div class="owner-name">Tim Marlow</div>
      <div class="company-name">Heron Property Inspections, LLC</div>
    </div>

    <div class="role">
      <div class="role-name">Employee name</div>
      <div class="role-title">Managing Director</div>
    </div>

    <div class="contact-row" style="top:318px">
      <svg class="contact-icon" width="40" height="40" viewBox="0 0 40 40" fill="none" stroke="#fff" stroke-width="2">
        <circle cx="20" cy="20" r="18"/>
        <rect x="14" y="12" width="12" height="16" rx="2"/>
      </svg>
      703-555-0192
    </div>
    <div class="contact-row" style="top:376px">
      <svg class="contact-icon" width="40" height="40" viewBox="0 0 40 40" fill="none" stroke="#fff" stroke-width="2">
        <circle cx="20" cy="20" r="18"/>
        <rect x="11" y="14" width="18" height="12"/>
        <polyline points="11,14 20,21 29,14"/>
      </svg>
      tkmarlow@postvale.net
    </div>
    <div class="contact-row last" style="top:434px">
      <svg class="contact-icon" width="40" height="40" viewBox="0 0 40 40" fill="none" stroke="#fff" stroke-width="2">
        <circle cx="20" cy="20" r="18"/>
        <path d="M20 29 C14 22 13 19 13 17 A7 7 0 0 1 27 17 C27 19 26 22 20 29 Z"/>
        <circle cx="20" cy="17" r="2.5"/>
      </svg>
      7182 Quarry Lane Fernhill, Virginia 20148
    </div>
  </div>
</body>
</html>
```